Wine Label Design

A wine label for 750ml bottles. Same label for different varieties with the variety / region / vintage to be updated as required.
Brand: Beyond the Ridge
Product Use: Front and Back label suitable for a 750 ml bottle (preferably Burgundy bottles)
Design Brief: Beyond the Ridge is a small winery that produces limited amounts of hand crafted wines that are aimed at the mid to top end of the market and requires a label befitting the work that goes into the creation of the wine. In terms of style i don't have any preconceptions and am open to a broad range of design suggestions at the same level of existing premium brands or innovative brands.
Must Have for Front label
Front Label
Beyond the Ridge
2013
Grampians
Shiraz
750ML (should be in smaller text)
Alc. 14% by Vol. (should be in smaller text)
Must Have for Back Label
Beyond the Ridge
2013
Grampians
Shiraz
www.beyondtheridge.com.au (should be in smaller text)
Product of Australia
Alc.14% by Vol. (should be in smaller text)
Contains preservative 220(should be in smaller text)
Below are some guides for dimensions:
The Front Label Size can be between
100 - 120 mm (Width) x 70 - 85 mm (Height)
The back label size can be between
90 mm (Width) x 70 - 85 mm (Height)
Updates
Target Market(s)
Medium to top end of the wine market who require the label to be a reflection of the wine.
Industry/Entity Type
Product
Colors
Designer to choose colors to be used in the design.
Look and feel
Each slider illustrates characteristics of the customer's brand and the style your logo design should communicate.

```html
<!DOCTYPE html>
<html lang="en">
<head>
<meta charset="utf-8">
<title>Beyond the Ridge – Front Label</title>
<link rel="stylesheet" href="https://fonts.googleapis.com/css2?family=Poiret+One&display=swap">
<style>
  :root {
    --paper: #f3ede3;
    --paper-shade: #ebe3d6;
    --ink: #1c1c1c;
    --ink-soft: #3a3634;
    --flourish: #cdc3b8;
  }
  * { margin: 0; padding: 0; box-sizing: border-box; }
  html, body { width: 855px; height: 1200px; overflow: hidden; background: var(--paper); }
  .label {
    position: relative;
    width: 855px;
    height: 1200px;
    background: radial-gradient(ellipse at 50% 45%, var(--paper) 0%, var(--paper-shade) 100%);
    font-family: "Poiret One", "Century Gothic", sans-serif;
    color: var(--ink);
  }
  .label__frame {
    position: absolute;
    left: 20px; top: 17px; right: 23px; bottom: 23px;
    border: 6px solid var(--ink);
  }
  .flourish {
    position: absolute;
    opacity: 0.55;
  }
  .flourish--top-right {
    left: 470px; top: 23px; width: 356px; height: 500px;
    background: radial-gradient(ellipse at 70% 45%, var(--flourish) 0%, rgba(205,195,184,0.35) 45%, rgba(205,195,184,0) 72%);
  }
  .flourish--bottom-left {
    left: 26px; top: 740px; width: 360px; height: 410px;
    background: radial-gradient(ellipse at 40% 45%, var(--flourish) 0%, rgba(205,195,184,0.35) 45%, rgba(205,195,184,0) 72%);
  }
  .label__text {
    position: absolute;
    left: 0; width: 100%;
    text-align: center;
    line-height: 1;
  }
  .brand-name {
    top: 190px;
    font-size: 88px;
    letter-spacing: 1px;
    color: var(--ink);
  }
  .brand-rule {
    position: absolute;
    left: 114px; top: 304px;
  }
  .vintage {
    top: 362px;
    font-size: 66px;
    color: var(--ink-soft);
  }
  .region {
    top: 708px;
    font-size: 52px;
    color: var(--ink-soft);
  }
  .variety {
    top: 864px;
    font-size: 52px;
    color: var(--ink-soft);
  }
  .volume {
    top: 1020px;
    font-size: 18px;
    color: var(--ink-soft);
  }
  .alcohol {
    top: 1092px;
    font-size: 18px;
    color: var(--ink-soft);
  }
</style>
</head>
<body>
  <main class="label">
    <div class="flourish flourish--top-right" role="img" aria-label="Decorative acanthus scroll ornament"></div>
    <div class="flourish flourish--bottom-left" role="img" aria-label="Decorative acanthus scroll ornament"></div>
    <div class="label__frame"></div>

    <h1 class="label__text brand-name">Beyond the Ridge</h1>
    <svg class="brand-rule" width="663" height="14" viewBox="0 0 663 14" aria-hidden="true">
      <rect x="0" y="2" width="663" height="2" fill="#1c1c1c"/>
      <rect x="0" y="9" width="663" height="4" fill="#1c1c1c"/>
    </svg>
    <p class="label__text vintage">2013</p>

    <p class="label__text region">Grampians</p>
    <p class="label__text variety">Shiraz</p>

    <p class="label__text volume">750ML</p>
    <p class="label__text alcohol">Alc. 14% by Vol.</p>
  </main>
</body>
</html>
```